Website for my photography business

I need a website for my photography business, Bram Kellet Photography. I need a website that has a landing page with a cover photo of each kind of photography I do. For example, Nature, Weddings, Portraits and Architecture. I want it so that when someone comes onto my website they have to choose which kind of photography page they want to visit. So if they click on the wedding photo it will open to a page with my wedding portfolio images and a contact me button. If they choose nature photography I want them to be redirected to an e-commerce section where they can purchase prints. Architecture and Portraits should open up to their respective portfolios with about me and contact info. I like this kind of format because I want people who come to my website for a specific type of photography to be able to be directed there easily without having to look at a mix of other kinds of photography. I will provide a few files to use as placeholders. I have already purchased the bramkelletphotography.example domain name. A Wix website would be great because I am most familiar with it but I am open to anything.

Industry/Entity Type

Photographer

Number of Pages Required

5+ page

Requirements
Must have
• Landing Page and e-commerce

```html
<!DOCTYPE html>
<html lang="en">
<head>
<meta charset="utf-8">
<title>Bram Kellet Photography</title>
<link href="https://fonts.googleapis.com/css2?family=Montserrat:wght@300;400;500;600;700&display=swap" rel="stylesheet">
<style>
:root{
  --bg:#f4f4f4;
  --ink:#222;
  --muted:#6a6a6a;
  --teal:#2c6b7a;
  --navy:#1c4763;
  --gold:#e3a511;
  --share:#3e5f70;
  --dark:#111;
  --field:#1a1a1a;
  --line:#3a3a3a;
}
*{box-sizing:border-box;margin:0;padding:0}
html,body{width:1200px;height:3375px;overflow:hidden}
body{background:var(--bg);font-family:"Montserrat",sans-serif;color:var(--ink);position:relative}

/* navigation */
.site-nav{position:absolute;left:0;top:0;width:1200px;height:75px;background:#fff}
.nav-link{position:absolute;top:36px;font-size:10.5px;font-weight:500;letter-spacing:.4px;color:#333;text-transform:uppercase}
.nav-link.active{color:var(--teal)}
.brand{position:absolute;left:511px;top:9px;width:179px;height:57px;border:1px solid #ddd;display:flex;align-items:center;justify-content:center;font-size:11px;font-weight:500;color:var(--navy);letter-spacing:.3px}

/* hero */
.hero{position:absolute;left:0;top:75px;width:1200px;height:606px;clip-path:polygon(0 0,100% 0,100% 86%,0 100%);
  background:linear-gradient(180deg,#36442f 0%,#55624a 30%,#a9b0aa 50%,#e4e9ee 65%,#f3f6f9 100%)}
.hero-dots{position:absolute;left:22px;top:310px;width:10px}
.hero-dots span{display:block;width:9px;height:9px;border:1.5px solid #fff;border-radius:50%;margin-bottom:8px}
.hero-dots span.on{border-color:var(--gold)}
.hero-panel{position:absolute;left:432px;top:249px;width:334px;height:194px;background:rgba(205,205,205,.85)}
.hero-panel .frame{position:absolute;left:9px;top:10px;right:9px;bottom:10px;border-left:2px solid #444;border-right:2px solid #444}
.hero-panel .frame::before,.hero-panel .frame::after{content:"";position:absolute;left:-6px;right:-6px;height:1px;background:#444}
.hero-panel .frame::before{top:4px}.hero-panel .frame::after{bottom:4px}
.hero-welcome{position:absolute;left:0;width:100%;top:34px;text-align:center;font-size:15px;letter-spacing:1px;color:#333}
.hero-title{position:absolute;left:0;width:100%;top:57px;text-align:center;font-size:29px;line-height:36px;font-weight:700;letter-spacing:2px;color:var(--teal)}
.hero-btn{position:absolute;left:110px;top:140px;width:95px;height:24px;border:2px solid #333;font-size:11px;display:flex;align-items:center;justify-content:center;color:#222}

/* categories */
.category{position:absolute;left:0;width:1200px;height:441px}
.photo{position:absolute;top:0;width:600px;height:441px}
.photo-weddings{background:linear-gradient(135deg,#a89482 0%,#bca894 50%,#8f7b6c 100%)}
.photo-nature{background:linear-gradient(135deg,#6b3f1c 0%,#a9652a 45%,#7b6a30 100%)}
.photo-architecture{background:linear-gradient(180deg,#d6d9dc 0%,#a87a64 45%,#8b8780 75%,#7a8e5c 100%)}
.photo-portraits{background:linear-gradient(135deg,#2a2a2a 0%,#7a7a7a 55%,#3a3a3a 100%)}
.share{position:absolute;top:8px;width:46px;height:46px;background:var(--share);display:flex;align-items:center;justify-content:center}
.cat-text{position:absolute;top:0;width:460px}
.crumbs{position:absolute;top:92px;font-size:11px;color:var(--navy)}
.cat-title{position:absolute;top:117px;font-size:27px;font-weight:600;letter-spacing:2.5px;color:#222}
.cat-copy{position:absolute;top:172px;width:440px;font-size:11.6px;line-height:16.5px;letter-spacing:.5px;color:var(--muted);font-weight:400}
.btn-gallery{position:absolute;top:301px;width:140px;height:35px;border:1px solid var(--navy);outline:1px solid var(--navy);outline-offset:-4px;display:flex;align-items:center;justify-content:center;font-size:11.5px;font-weight:700;letter-spacing:1px;color:var(--navy)}
.btn-gallery.gold{border-color:var(--gold);outline-color:var(--gold);color:var(--gold)}

/* testimonials */
.reviews{position:absolute;left:0;top:2446px;width:1200px;height:432px}
.eyebrow{position:absolute;top:57px;width:100%;text-align:center;font-size:9px;font-weight:600;letter-spacing:.5px}
.reviews-title{position:absolute;top:71px;width:100%;text-align:center;font-size:16px;font-weight:700;letter-spacing:2px}
.reviews-title span{position:relative}
.reviews-title span::after{content:"";position:absolute;left:0;bottom:-3px;width:60px;height:2px;background:var(--gold)}
.reviews-intro{position:absolute;top:104px;left:180px;width:840px;text-align:center;font-size:11px;line-height:17px;color:var(--muted)}
.review{position:absolute;top:165px;width:293px;height:148px;background:#f6f6f6;border:1px solid #e2e2e2;box-shadow:0 1px 3px rgba(0,0,0,.08)}
.quote{position:absolute;top:-24px;left:0;width:100%;text-align:center;font-size:60px;line-height:60px;color:#cfcfcf;font-family:Georgia,serif}
.review p{position:absolute;top:34px;left:18px;right:18px;text-align:center;font-size:11px;line-height:16.5px;color:#444}
.reviewer{position:absolute;top:330px;height:40px}
.avatar{position:absolute;left:0;top:0;width:38px;height:38px;border-radius:50%;background:#cfe2f3;border:3px solid #4d8fc4}
.reviewer b{position:absolute;left:47px;top:8px;font-size:11px;font-weight:600;color:var(--navy);white-space:nowrap}
.reviewer small{position:absolute;left:47px;top:22px;font-size:9.5px;color:#888;white-space:nowrap}
.pager{position:absolute;top:390px;left:580px}
.pager span{display:inline-block;width:10px;height:10px;border:1px solid var(--navy);border-radius:50%;margin-right:3px}
.pager span.on{background:radial-gradient(circle,var(--navy) 45%,transparent 50%)}

/* contact */
.ask{position:absolute;left:0;top:2878px;width:1200px;height:364px;background:var(--dark)}
.ask-photo{position:absolute;left:0;top:0;width:600px;height:364px;background:linear-gradient(135deg,#3a2a1f 0%,#6e5846 50%,#2e2118 100%)}
.ask-title{position:absolute;left:672px;top:20px;font-size:23px;font-weight:500;letter-spacing:1px;color:#eee}
.field{position:absolute;left:672px;width:327px;height:32px;border:1px solid var(--line);background:var(--field)}
.field .ico{position:absolute;left:0;top:0;width:40px;height:100%;border-right:1px solid var(--line);display:flex;align-items:center;justify-content:center}
.field span{position:absolute;left:47px;top:10px;font-size:10.5px;color:#ddd}
.submit{position:absolute;left:779px;top:318px;width:99px;height:29px;border:1px solid var(--navy);outline:1px solid var(--navy);outline-offset:-4px;display:flex;align-items:center;justify-content:center;font-size:11px;letter-spacing:1px;color:var(--navy)}

/* footer */
.site-footer{position:absolute;left:0;top:3242px;width:1200px;height:133px;background:var(--bg)}
.footer-links{position:absolute;top:27px;width:100%;text-align:center;font-size:11.5px;color:#333}
.footer-links i{font-style:normal;color:#999;margin:0 12px;font-size:9px}
.socials{position:absolute;top:62px;left:525px}
.socials span{display:inline-block;width:27px;height:27px;border-radius:50%;background:#fff;border:1px solid #ddd;margin-right:9px}
.copyright{position:absolute;top:108px;width:100%;text-align:center;font-size:9px;color:#444}
</style>
</head>
<body>

<header class="site-nav">
  <span class="nav-link active" style="left:185px">Home</span>
  <span class="nav-link" style="left:249px">Our Story</span>
  <span class="nav-link" style="left:341px">Our Services &#8964;</span>
  <div class="brand">Bram Kellet Photography</div>
  <span class="nav-link" style="left:794px">Gallery</span>
  <span class="nav-link" style="left:875px">News</span>
  <span class="nav-link" style="left:938px">Contact Us</span>
</header>

<section class="hero" role="img" aria-label="Cover photo: wildlife resting on snowy rocks in front of pine trees"></section>
<div class="hero-dots"><span></span><span></span><span class="on"></span><span></span><span></span><span></span><span></span><span></span></div>
<div class="hero-panel">
  <div class="frame"></div>
  <div class="hero-welcome">WELCOME TO</div>
  <div class="hero-title">BRAM KELLET<br>PHOTOGRAPHY</div>
  <div class="hero-btn">Contact Us</div>
</div>

<section class="category" style="top:681px">
  <div class="photo photo-weddings" style="left:0" role="img" aria-label="Wedding photo: rings on granite"></div>
  <div class="share" style="left:546px"><svg width="22" height="20" viewBox="0 0 22 20"><rect x="1" y="5" width="14" height="13" fill="none" stroke="#fff" stroke-width="2"/><path d="M7 12c1-5 5-7 10-7V2l4 4-4 4V7c-4 0-7 1-10 5z" fill="#fff"/></svg></div>
  <div class="cat-text" style="left:629px">
    <div class="crumbs">Landscape / Weddings</div>
    <div class="cat-title">WEDDINGS</div>
    <p class="cat-copy">Lorem ipsum dolor sit amet, consectetur adipiscing elit, sed do eiusmod tempor incididunt ut labore et dolore magna aliqua. Ut enim ad minim veniam, quis nostrud exercitation ullamco laboris nisi ut aliquip ex ea commodo consequat. Duis aute irure dolor in reprehenderit in voluptate velit esse cillum dolore eu fugiat nulla pariatur. Excepteur sint occaecat cupidatat non proident, sunt in culpa qui officia deserunt mollit anim id est laborum.</p>
    <div class="btn-gallery gold">VIEW GALLERY</div>
  </div>
</section>

<section class="category" style="top:1123px">
  <div class="cat-text" style="left:126px">
    <div class="crumbs">Portraits / Nature</div>
    <div class="cat-title">NATURE</div>
    <p class="cat-copy">Lorem ipsum dolor sit amet, consectetur adipiscing elit, sed do eiusmod tempor incididunt ut labore et dolore magna aliqua. Ut enim ad minim veniam, quis nostrud exercitation ullamco laboris nisi ut aliquip ex ea commodo consequat. Duis aute irure dolor in reprehenderit in voluptate velit esse cillum dolore eu fugiat nulla pariatur. Excepteur sint occaecat cupidatat non proident, sunt in culpa qui officia deserunt mollit anim id est laborum.</p>
    <div class="btn-gallery">VIEW GALLERY</div>
  </div>
  <div class="photo photo-nature" style="left:600px" role="img" aria-label="Nature photo: autumn forest path"></div>
  <div class="share" style="left:606px"><svg width="22" height="20" viewBox="0 0 22 20"><rect x="1" y="5" width="14" height="13" fill="none" stroke="#fff" stroke-width="2"/><path d="M7 12c1-5 5-7 10-7V2l4 4-4 4V7c-4 0-7 1-10 5z" fill="#fff"/></svg></div>
</section>

<section class="category" style="top:1564px">
  <div class="photo photo-architecture" style="left:0" role="img" aria-label="Architecture photo: brick and glass campus building"></div>
  <div class="share" style="left:546px"><svg width="22" height="20" viewBox="0 0 22 20"><rect x="1" y="5" width="14" height="13" fill="none" stroke="#fff" stroke-width="2"/><path d="M7 12c1-5 5-7 10-7V2l4 4-4 4V7c-4 0-7 1-10 5z" fill="#fff"/></svg></div>
  <div class="cat-text" style="left:629px">
    <div class="crumbs">Landscape / Architecture</div>
    <div class="cat-title">ARCHITECTURE</div>
    <p class="cat-copy">Lorem ipsum dolor sit amet, consectetur adipiscing elit, sed do eiusmod tempor incididunt ut labore et dolore magna aliqua. Ut enim ad minim veniam, quis nostrud exercitation ullamco laboris nisi ut aliquip ex ea commodo consequat. Duis aute irure dolor in reprehenderit in voluptate velit esse cillum dolore eu fugiat nulla pariatur. Excepteur sint occaecat cupidatat non proident, sunt in culpa qui officia deserunt mollit anim id est laborum.</p>
    <div class="btn-gallery">VIEW GALLERY</div>
  </div>
</section>

<section class="category" style="top:2004px">
  <div class="cat-text" style="left:126px">
    <div class="crumbs">Landscape / Portraits</div>
    <div class="cat-title">PORTRAITS</div>
    <p class="cat-copy">Lorem ipsum dolor sit amet, consectetur adipiscing elit, sed do eiusmod tempor incididunt ut labore et dolore magna aliqua. Ut enim ad minim veniam, quis nostrud exercitation ullamco laboris nisi ut aliquip ex ea commodo consequat. Duis aute irure dolor in reprehenderit in voluptate velit esse cillum dolore eu fugiat nulla pariatur. Excepteur sint occaecat cupidatat non proident, sunt in culpa qui officia deserunt mollit anim id est laborum.</p>
    <div class="btn-gallery">VIEW GALLERY</div>
  </div>
  <div class="photo photo-portraits" style="left:600px" role="img" aria-label="Portrait photo: black and white figure study"></div>
  <div class="share" style="left:606px"><svg width="22" height="20" viewBox="0 0 22 20"><rect x="1" y="5" width="14" height="13" fill="none" stroke="#fff" stroke-width="2"/><path d="M7 12c1-5 5-7 10-7V2l4 4-4 4V7c-4 0-7 1-10 5z" fill="#fff"/></svg></div>
</section>

<section class="reviews">
  <div class="eyebrow">OUR NEWS</div>
  <div class="reviews-title"><span>WHAT'S CLIENT SAYS</span></div>
  <p class="reviews-intro">Sed ut perspiciatis unde omnis iste natus error sit voluptatem accusantium doloremque laudantium, totam rem aperiam, eaque ipsa quae ab illo inventore veritatis et quasi architecto beatae</p>

  <div class="review" style="left:139px"><div class="quote">&#8220;</div><p>Lorem ipsum dolor sit amet, consectetur adipiscing elit, sed do eiusmod tempor incididunt ut labore et dolore magna aliqua. Ut enim ad minim veniam, quis nostrud exercitation ullamco laboris nisi ut aliquip ex ea commodo consequat.</p></div>
  <div class="review" style="left:453px"><div class="quote">&#8220;</div><p>Lorem ipsum dolor sit amet, consectetur adipiscing elit, sed do eiusmod tempor incididunt ut labore et dolore magna aliqua. Ut enim ad minim veniam, quis nostrud exercitation ullamco laboris nisi ut aliquip ex ea commodo consequat.</p></div>
  <div class="review" style="left:768px"><div class="quote">&#8220;</div><p>Lorem ipsum dolor sit amet, consectetur adipiscing elit, sed do eiusmod tempor incididunt ut labore et dolore magna aliqua. Ut enim ad minim veniam, quis nostrud exercitation ullamco laboris nisi ut aliquip ex ea commodo consequat.</p></div>

  <div class="reviewer" style="left:208px"><div class="avatar"></div><b>Corin T. Walsh</b><small>Lorem ipsum dolor</small></div>
  <div class="reviewer" style="left:523px"><div class="avatar"></div><b>Dario M. Lund</b><small>Lorem ipsum dolor</small></div>
  <div class="reviewer" style="left:838px"><div class="avatar"></div><b>Neil R. Haskett</b><small>Lorem ipsum dolor</small></div>

  <div class="pager"><span></span><span class="on"></span><span></span></div>
</section>

<section class="ask">
  <div class="ask-photo" role="img" aria-label="Wedding photo: couple on a carved staircase"></div>
  <h2 class="ask-title">Ask Your Question</h2>
  <div class="field" style="top:54px"><div class="ico"><svg width="12" height="12" viewBox="0 0 12 12"><circle cx="6" cy="3.5" r="3" fill="#ddd"/><path d="M0 12c0-4 3-5 6-5s6 1 6 5z" fill="#ddd"/></svg></div><span>Name*</span></div>
  <div class="field" style="top:96px"><div class="ico"><svg width="13" height="10" viewBox="0 0 13 10"><rect x=".5" y=".5" width="12" height="9" fill="none" stroke="#ddd"/><path d="M.5 .5l6 5 6-5" fill="none" stroke="#ddd"/></svg></div><span>Email*</span></div>
  <div class="field" style="top:137px"><div class="ico"><svg width="12" height="12" viewBox="0 0 12 12"><path d="M2 0l3 3-1.5 2a7 7 0 003.5 3.5L9 7l3 3-2 2C5 12 0 7 0 2z" fill="#ddd"/></svg></div><span>Phone*</span></div>
  <div class="field" style="top:179px"><div class="ico"><svg width="11" height="12" viewBox="0 0 11 12"><path d="M2 0h9v10H2a1 1 0 000 2h9v-1H2" fill="none" stroke="#ddd" stroke-width="1.5"/></svg></div><span>Subject*</span></div>
  <div class="field" style="top:221px;height:78px"><div class="ico" style="align-items:flex-start;padding-top:10px"><svg width="13" height="11" viewBox="0 0 13 11"><ellipse cx="6.5" cy="4.5" rx="6" ry="4" fill="none" stroke="#ddd"/><path d="M3 8l-1 3 3-2" fill="none" stroke="#ddd"/></svg></div><span>Message*</span></div>
  <div class="submit">SUBMIT</div>
</section>

<footer class="site-footer">
  <div class="footer-links">Home<i>::</i>Our Story<i>::</i>Our Services<i>::</i>Gallery<i>::</i>News<i>::</i>Contact us</div>
  <div class="socials"><span></span><span></span><span></span><span></span></div>
  <div class="copyright">&copy; Copyright Company name 2020, All Rights Reserved</div>
</footer>

</body>
</html>
```